Halvery Construction Group Website

Need a dynamic corporate website that can be built on with time. We want to get our information out to the world and have a place where customers can submit requests for proposals.

Target Market(s)

Custom home owners and buyers. Architects and Real Estate Agents.

Industry/Entity Type

Construction

Number of Pages Required

3 page

Font styles to use
Serif
Sans Serif

Requirements
Must have
• Company logo, about, company contact information, biography, contact, projects,
• Sleek, modern, clean, attractive design.
• Online form customers can use for filling out a request for project proposal.
• Linkedin hyperlink.
• Uses www.halveryconstructiongroup.example

```html
<!DOCTYPE html>
<html lang="en">
<head>
<meta charset="utf-8">
<title>Halvery Construction Group</title>
<link href="https://fonts.googleapis.com/css2?family=Raleway:wght@300;400;500;600;700&family=Open+Sans:wght@400;600&display=swap" rel="stylesheet">
<style>
:root{
  --navy:#1f3a8f;
  --navy-dark:#1a2d78;
  --navy-deep:#172a6e;
  --sky:#2b9fdc;
  --sky-light:#4fb3e8;
  --grey-bg:#eef0f4;
  --text:#4a4f5c;
  --muted:#8a8f9a;
  --white:#ffffff;
}
*{margin:0;padding:0;box-sizing:border-box}
html,body{width:1200px;height:3028px;overflow:hidden}
body{font-family:"Open Sans",Arial,sans-serif;color:var(--text);background:var(--white)}
h1,h2,h3,h4,.btn,.nav a{font-family:"Raleway",Arial,sans-serif}
.btn{display:inline-block;background:var(--sky);color:var(--white);font-size:15px;font-weight:600;letter-spacing:1px;padding:14px 28px;text-transform:uppercase;border-radius:3px}

/* header */
.site-header{height:108px;display:flex;align-items:center;justify-content:space-between;padding:0 72px}
.brand{display:flex;align-items:center;gap:14px}
.brand-square{width:52px;height:52px;background:var(--navy)}
.brand-name{font-family:"Raleway",sans-serif;font-weight:700;font-size:34px;color:var(--navy);letter-spacing:1px;line-height:1}
.brand-sub{font-family:"Raleway",sans-serif;font-weight:700;font-size:13px;color:var(--navy);letter-spacing:1.5px}
.header-right{display:flex;align-items:center;gap:34px}
.call{display:flex;align-items:center;gap:12px}
.call small{display:block;font-size:13px;color:var(--text)}
.call strong{display:block;font-family:"Raleway",sans-serif;font-size:28px;color:var(--sky);font-weight:600;line-height:1.1}
.btn-quote{background:var(--navy);padding:14px 22px}

/* nav */
.nav{height:68px;background:var(--navy);display:flex;align-items:center;padding:0 72px}
.nav a{color:var(--white);text-decoration:none;font-size:15px;font-weight:500;letter-spacing:1px;padding:0 28px;height:68px;display:flex;align-items:center}
.nav a.active{background:var(--sky)}
.nav .search{margin-left:auto}

/* hero */
.hero{position:relative;height:504px;background:linear-gradient(100deg,#5d7386 0%,#9fb6c8 30%,#d8e4ee 60%,#eef3f7 100%);overflow:hidden}
.hero-text{position:absolute;right:72px;top:120px;text-align:right;width:560px}
.hero-text h1{font-size:64px;font-weight:600;color:var(--navy);line-height:1}
.hero-text h2{font-size:34px;font-weight:500;color:var(--navy);margin-top:6px}
.hero-text p{font-size:15px;line-height:1.5;color:var(--navy-deep);margin:10px 0 30px}
.arrow{position:absolute;top:220px;width:50px;height:50px;border-radius:50%;background:rgba(255,255,255,.85);display:flex;align-items:center;justify-content:center}
.arrow.left{left:14px}.arrow.right{right:14px}

/* services */
.services{height:368px;background:var(--grey-bg);display:flex;justify-content:center;gap:40px;padding-top:56px}
.service{width:230px;text-align:center}
.service-icon{width:112px;height:112px;border-radius:50%;background:var(--navy);margin:0 auto 18px;display:flex;align-items:center;justify-content:center;border:6px solid #dfe3ec}
.service h3{color:var(--sky);font-size:19px;font-weight:600}
.service p{font-size:14px;color:var(--muted);line-height:1.5;margin-top:8px}

/* welcome */
.welcome{height:392px;display:flex;align-items:center;padding:0 72px;gap:120px}
.welcome-body{width:760px}
.eyebrow{color:var(--sky);font-family:"Raleway",sans-serif;font-size:15px;letter-spacing:1px;text-transform:uppercase}
.welcome h2{font-size:40px;color:var(--navy);font-weight:500;margin:4px 0 18px}
.welcome p{font-size:14px;line-height:1.7;margin-bottom:14px}
.welcome-mark{display:flex;align-items:center;gap:14px}
.welcome-mark .sq{width:60px;height:60px;background:var(--navy)}
.welcome-mark span{font-family:"Raleway",sans-serif;font-weight:700;font-size:44px;color:var(--navy)}

/* projects */
.projects{height:600px;background:linear-gradient(180deg,#2a3f98,#233687);text-align:center;padding-top:46px;color:var(--white)}
.projects h2{font-size:52px;font-weight:500;margin:2px 0 30px}
.project-grid{display:flex;justify-content:center;gap:12px}
.project{width:252px;text-align:center}
.project-photo{height:164px;border:4px solid var(--white)}
.project h3{color:var(--sky-light);font-size:19px;font-weight:600;margin-top:12px;text-transform:uppercase}
.project p{font-size:14px;line-height:1.5;margin-top:6px}
.projects .btn{margin-top:30px}

/* cta band */
.cta{height:240px;background:var(--sky);display:flex;align-items:center;justify-content:space-between;padding:0 72px;color:var(--white)}
.cta h2{font-size:34px;font-weight:500}
.cta p{font-size:15px;line-height:1.6;margin-top:10px;width:760px}
.cta .btn{background:var(--navy)}

/* contact */
.contact{position:relative;height:520px;background:linear-gradient(180deg,#f4f6fa,#ffffff)}
.contact-head{position:absolute;left:272px;top:30px;width:380px;text-align:center}
.contact-head h2{font-size:46px;color:var(--navy-deep);font-weight:500}
.contact-form{position:absolute;left:272px;top:120px;width:368px;height:384px;border:6px solid var(--navy-deep);background:var(--white);padding:22px}
.field{border:1px solid #c8ccd6;height:42px;margin-bottom:14px;font-size:13px;color:var(--muted);padding:11px 12px}
.field.tall{height:112px}
.contact-form .btn{display:block;width:112px;margin:10px auto 0;text-align:center;padding:12px 0}
.contact-photo{position:absolute;left:720px;top:20px;width:380px;height:500px;background:linear-gradient(180deg,#e8edf3,#c5ccd6 60%,#3c69b0 100%);border-radius:190px 190px 0 0}

/* footer */
.footer{height:228px;background:var(--navy-deep);color:var(--white);padding:30px 72px}
.footer-nav{display:flex;align-items:center;gap:6px}
.footer-nav a{color:var(--white);text-decoration:none;font-size:14px;padding:8px 18px;font-family:"Raleway",sans-serif}
.footer-nav a.active{border:1px solid var(--white)}
.social{margin-left:auto;display:flex;gap:10px}
.social span{width:36px;height:36px;border-radius:50%;background:var(--sky)}
.footer-info{display:flex;gap:50px;margin-top:60px;font-size:13px;align-items:flex-start}
.footer-info div{display:flex;gap:10px;align-items:flex-start;line-height:1.5}
.footer-info .copy{margin-left:auto;width:220px}
</style>
</head>
<body>

<header class="site-header">
  <div class="brand">
    <div class="brand-square"></div>
    <div>
      <div class="brand-name">HALVERY</div>
      <div class="brand-sub">CONSTRUCTION GROUP, INC.</div>
    </div>
  </div>
  <div class="header-right">
    <div class="call">
      <svg width="34" height="34" viewBox="0 0 24 24"><path fill="#1f3a8f" d="M6.6 10.8a15 15 0 006.6 6.6l2.2-2.2a1 1 0 011-.25 11.4 11.4 0 003.6.57 1 1 0 011 1V20a1 1 0 01-1 1A17 17 0 013 4a1 1 0 011-1h3.5a1 1 0 011 1c0 1.25.2 2.45.57 3.57a1 1 0 01-.25 1z"/></svg>
      <div><small>Call Us Know</small><strong>123 456 7890</strong></div>
    </div>
    <span class="btn btn-quote">GET A QUOTE</span>
  </div>
</header>

<nav class="nav">
  <a class="active">HOME</a><a>ABOUT</a><a>SERVICES</a><a>BIOGRAPHY</a><a>PROJECTS</a><a>CONTACT US</a>
  <span class="search"><svg width="22" height="22" viewBox="0 0 24 24"><circle cx="10" cy="10" r="7" fill="none" stroke="#fff" stroke-width="2.5"/><line x1="15" y1="15" x2="21" y2="21" stroke="#fff" stroke-width="2.5"/></svg></span>
</nav>

<section class="hero" role="img" aria-label="Glass office tower under construction with a tower crane against the sky">
  <span class="arrow left"><svg width="18" height="18" viewBox="0 0 24 24"><path d="M15 4 7 12l8 8" fill="none" stroke="#1f3a8f" stroke-width="3"/></svg></span>
  <div class="hero-text">
    <h1>HALVERY</h1>
    <h2>CONSTRUCTION GROUP, INC.</h2>
    <p>We plan and build custom homes with care, from the first sketch to the final walkthrough, for owners, architects and agents alike.</p>
    <span class="btn">CONTACT US KNOW</span>
  </div>
  <span class="arrow right"><svg width="18" height="18" viewBox="0 0 24 24"><path d="M9 4l8 8-8 8" fill="none" stroke="#1f3a8f" stroke-width="3"/></svg></span>
</section>

<section class="services">
  <div class="service">
    <div class="service-icon"><svg width="50" height="50" viewBox="0 0 24 24"><path fill="#fff" d="M12 3 2 12h3v8h5v-5h4v5h5v-8h3z"/></svg></div>
    <h3>LOREM IPSUMS TEXT</h3><p>Custom homes built to plan, on time and on budget.</p>
  </div>
  <div class="service">
    <div class="service-icon"><svg width="50" height="50" viewBox="0 0 24 24"><path fill="#fff" d="M4 21V9h6v12zM12 21V4h8v17zM6 11h2v2H6zm0 4h2v2H6zm8-9h2v2h-2zm0 4h2v2h-2zm0 4h2v2h-2z"/></svg></div>
    <h3>LOREM IPSUMS TEXT</h3><p>Commercial builds managed from permit to handover.</p>
  </div>
  <div class="service">
    <div class="service-icon"><svg width="50" height="50" viewBox="0 0 24 24"><circle cx="12" cy="12" r="7" fill="none" stroke="#fff" stroke-width="4" stroke-dasharray="3 2.5"/><circle cx="12" cy="12" r="3" fill="#fff"/></svg></div>
    <h3>LOREM IPSUMS TEXT</h3><p>Renovation and remodeling done with clean precision.</p>
  </div>
  <div class="service">
    <div class="service-icon"><svg width="50" height="50" viewBox="0 0 24 24"><path fill="#fff" d="M3 11 12 4l9 7v9H3z"/><rect x="10" y="13" width="4" height="7" fill="#1f3a8f"/></svg></div>
    <h3>LOREM IPSUMS TEXT</h3><p>Design support for architects and real estate agents.</p>
  </div>
</section>

<section class="welcome">
  <div class="welcome-body">
    <div class="eyebrow">Welcome to</div>
    <h2>HALVERY CONSTRUCTION GROUP, INC.</h2>
    <p>For over two decades our team has built custom homes and commercial spaces across the region. We work closely with owners, architects and agents to turn clear plans into lasting, well crafted buildings that stand the test of time.</p>
    <p>Every project gets a dedicated manager, honest pricing and steady communication, so you always know where your build stands from the ground up.</p>
    <span class="btn">KNOW MORE</span>
  </div>
  <div class="welcome-mark"><div class="sq"></div><span>Halvery</span></div>
</section>

<section class="projects">
  <div class="eyebrow" style="color:#4fb3e8">What we do</div>
  <h2>OUR PROJECTS</h2>
  <div class="project-grid">
    <div class="project"><div class="project-photo" role="img" aria-label="Crew working on a house frame" style="background:linear-gradient(160deg,#d9dfe6,#9aa7b5)"></div><h3>Project Title</h3><p>A family home framed and finished in eight months.</p></div>
    <div class="project"><div class="project-photo" role="img" aria-label="Timber house under construction" style="background:linear-gradient(160deg,#8fb6dd,#b48a5e)"></div><h3>Project Title</h3><p>A timber residence built on a sloping lakeside lot.</p></div>
    <div class="project"><div class="project-photo" role="img" aria-label="Bright empty interior with large windows" style="background:linear-gradient(160deg,#f0f1f3,#a9adb3)"></div><h3>Project Title</h3><p>An open interior fit out with wide glazed walls.</p></div>
    <div class="project"><div class="project-photo" role="img" aria-label="Modern commercial building exterior" style="background:linear-gradient(160deg,#8ab7e2,#b59a84)"></div><h3>Project Title</h3><p>A retail building delivered ahead of schedule.</p></div>
  </div>
  <span class="btn">VIEW ALL</span>
</section>

<section class="cta">
  <div>
    <h2>HALVERY CONSTRUCTION GROUP, INC.</h2>
    <p>Ready to start your next build? Send us your plans and we will prepare a clear, detailed proposal for your project within days.</p>
  </div>
  <span class="btn">GET A QUOTE</span>
</section>

<section class="contact">
  <div class="contact-head">
    <div class="eyebrow">Get in touch</div>
    <h2>CONTACT US</h2>
  </div>
  <form class="contact-form">
    <div class="field">Name*</div>
    <div class="field">Email*</div>
    <div class="field">Phone*</div>
    <div class="field tall">Message*</div>
    <span class="btn">SUBMIT</span>
  </form>
  <div class="contact-photo" role="img" aria-label="Smiling man in a checked shirt holding a laptop and giving a thumbs up"></div>
</section>

<footer class="footer">
  <div class="footer-nav">
    <a class="active">Home</a><a>About</a><a>Services</a><a>Biography</a><a>Projects</a><a>Contact</a>
    <div class="social"><span></span><span></span><span></span></div>
  </div>
  <div class="footer-info">
    <div><svg width="18" height="22" viewBox="0 0 24 24"><path fill="#fff" d="M12 2a7 7 0 00-7 7c0 5 7 13 7 13s7-8 7-13a7 7 0 00-7-7zm0 9.5A2.5 2.5 0 1112 6.5a2.5 2.5 0 010 5z"/></svg><span>101 - Oak Ridge Avenue,<br>Suite 200, Springvale</span></div>
    <div><svg width="18" height="18" viewBox="0 0 24 24"><path fill="#fff" d="M6.6 10.8a15 15 0 006.6 6.6l2.2-2.2a1 1 0 011-.25 11.4 11.4 0 003.6.57 1 1 0 011 1V20a1 1 0 01-1 1A17 17 0 013 4a1 1 0 011-1h3.5a1 1 0 011 1c0 1.25.2 2.45.57 3.57a1 1 0 01-.25 1z"/></svg><span>123 456 7890</span></div>
    <div><svg width="18" height="18" viewBox="0 0 24 24"><rect x="2" y="5" width="20" height="14" fill="none" stroke="#fff" stroke-width="2"/><path d="M2 6l10 7 10-7" fill="none" stroke="#fff" stroke-width="2"/></svg><span>info@halvery.example</span></div>
    <div class="copy"><span>©HALVERY - 2018, All rights reserved.</span></div>
  </div>
</footer>

</body>
</html>
```